Flat bootstrap design for existing site

I'm looking for a modern flat design based around an existing logo. This has to be a custom design (no external templates), and implemented into a bootstrap framework.

The logo is attached as 2 versions - choose whichever you want, that flows better with whatever design you choose.

Added screenshots of the existing site (currently using the default bootstrap layouts). Please make your designs around those pages in the screenshots (i.e. the homepage only has the postal code input and the header). The active page has 3 screenshots, because I wanted to illustrate the other states that would be visible (in the table rows).

This is a moving/junk removal website, just for some context.

Here's some example websites (flat designs) that I like, just to give you an idea of what I'm after.

https://www.plimvora.com/
https://dacklow.com/
https://trevanu.com/
https://quobrintal.com/en/

Coding

Coded - Design and coding required

Number of Pages Required

5+ page

Colors

Designer to choose colors to be used in the design.

Requirements
Must have
• It must be a modern/simple flat design, that is built around the existing logo (attached).
• It has to be implemented using bootstrap.

```html
<!DOCTYPE html>
<html lang="en">
<head>
<meta charset="utf-8">
<title>Bravuk — Booking Details</title>
<link rel="stylesheet" href="https://fonts.googleapis.com/css2?family=Lato:wght@400;700&family=Open+Sans:wght@400;600&display=swap">
<style>
  :root {
    --sky: #6fd0f2;
    --sky-deep: #5cc5ec;
    --accent: #45c3f0;
    --table-head: #229ac8;
    --ink: #333333;
    --text: #444444;
    --muted: #666666;
    --line: #cfcfcf;
    --field-border: #bdbdbd;
    --badge: #222222;
    --white: #ffffff;
  }
  * { box-sizing: border-box; margin: 0; padding: 0; }
  html, body { width: 1130px; height: 1200px; overflow: hidden; background: var(--white); }
  body { position: relative; font-family: "Open Sans", sans-serif; color: var(--text); }

  .site-header {
    position: absolute; left: 0; top: 0; width: 1130px; height: 99px;
  }
  .header-backdrop {
    position: absolute; inset: 0;
    background: linear-gradient(120deg, var(--sky-deep) 0%, var(--sky) 45%, var(--sky-deep) 100%);
  }
  .brand {
    position: absolute; left: 93px; top: 28px;
    font-family: "Lato", sans-serif; font-weight: 700; font-size: 40px;
    color: var(--white); letter-spacing: 1px; line-height: 1;
  }
  .main-nav {
    position: absolute; top: 35px; left: 0; width: 100%;
    font-family: "Lato", sans-serif; font-size: 15px; color: var(--white);
  }
  .main-nav a { position: absolute; color: var(--white); text-decoration: none; white-space: nowrap; }
  .nav-book { left: 520px; }
  .nav-how { left: 599px; }
  .nav-driver { left: 742px; padding-bottom: 4px; border-bottom: 1px solid var(--white); }
  .nav-account { left: 907px; top: -1px; font-size: 13px; }
  .nav-account svg { margin-left: 4px; vertical-align: middle; }

  .section-title {
    position: absolute; left: 0; width: 1130px; text-align: center;
    font-family: "Lato", sans-serif; font-weight: 700; font-size: 26px; color: var(--ink);
  }
  .booking-title { top: 198px; font-weight: 400; }
  .title-rule { position: absolute; left: 93px; top: 253px; width: 944px; height: 1px; background: var(--line); }

  .field-label { position: absolute; font-size: 12px; color: var(--muted); }
  .field {
    position: absolute; height: 39px; border: 1px solid var(--field-border);
    font-size: 12px; color: var(--text); display: flex; align-items: center; padding: 0 15px;
  }
  .field-package { left: 187px; top: 311px; width: 336px; justify-content: space-between; }
  .field-time { left: 607px; top: 311px; width: 336px; gap: 10px; }
  .field-description { left: 187px; top: 396px; width: 755px; height: 69px; align-items: flex-start; padding-top: 13px; }

  .update-button {
    position: absolute; left: 471px; top: 496px; width: 187px; height: 47px;
    background: var(--accent); color: var(--white); border-radius: 6px;
    font-family: "Open Sans", sans-serif; font-weight: 600; font-size: 13.5px;
    display: flex; align-items: center; justify-content: center; letter-spacing: -0.2px;
  }

  .drivers-title { top: 643px; }
  .drivers-note { position: absolute; top: 702px; left: 0; width: 1130px; text-align: center; font-size: 11.5px; color: var(--muted); }

  .drivers-table { position: absolute; left: 93px; top: 749px; width: 944px; }
  .table-head {
    height: 53px; background: var(--table-head); color: var(--white);
    font-weight: 600; font-size: 13px; position: relative;
  }
  .table-head span, .driver-row span { position: absolute; top: 50%; transform: translateY(-50%); white-space: nowrap; }
  .col-name { left: 16px; }
  .col-distance { left: 202px; }
  .col-time { left: 415px; }
  .driver-row { position: relative; height: 66px; font-size: 12px; color: var(--text); }
  .driver-row + .driver-row::before {
    content: ""; position: absolute; left: 9px; width: 945px; top: 0; height: 1px; background: var(--line);
  }
  .status-badge {
    left: 733px; width: 86px; height: 24px; background: var(--badge); color: var(--white);
    font-weight: 600; font-size: 13.5px; display: flex; align-items: center; justify-content: center;
  }

  .site-footer { position: absolute; left: 0; top: 1123px; width: 1130px; border-top: 2px solid #d6d6d6; }
  .copyright { padding-top: 29px; text-align: center; font-size: 12px; color: var(--muted); }
</style>
</head>
<body>
  <header class="site-header">
    <div class="header-backdrop" role="img" aria-label="Soft light-blue faceted background pattern"></div>
    <div class="brand">BRAVUK</div>
    <nav class="main-nav">
      <a class="nav-book">BOOK</a>
      <a class="nav-how">HOW IT WOWS</a>
      <a class="nav-driver">BECOME A DRIVER</a>
      <a class="nav-account">mara@plenvix.com<svg width="8" height="6" viewBox="0 0 8 6"><path d="M1 1.5l3 3 3-3" fill="none" stroke="#fff" stroke-width="1.2"/></svg></a>
    </nav>
  </header>

  <main>
    <h1 class="section-title booking-title">BOOKING DETAILS</h1>
    <div class="title-rule"></div>

    <label class="field-label" style="left:187px;top:287px;">Package selected:</label>
    <div class="field field-package">
      <span>Package 1</span>
      <svg width="9" height="6" viewBox="0 0 9 6"><path d="M1 1l3.5 3.5L8 1" fill="none" stroke="#555" stroke-width="1.2"/></svg>
    </div>

    <label class="field-label" style="left:607px;top:287px;">Pick-up time selected:</label>
    <div class="field field-time">
      <svg width="13" height="13" viewBox="0 0 13 13" fill="none" stroke="#777" stroke-width="1">
        <rect x="0.5" y="2" width="12" height="10.5"/><line x1="0.5" y1="5" x2="12.5" y2="5"/>
        <line x1="3.5" y1="0.5" x2="3.5" y2="3"/><line x1="9.5" y1="0.5" x2="9.5" y2="3"/>
        <line x1="4.5" y1="5" x2="4.5" y2="12.5"/><line x1="8.5" y1="5" x2="8.5" y2="12.5"/>
        <line x1="0.5" y1="8.7" x2="12.5" y2="8.7"/>
      </svg>
      <span>July 18 at 0:13 am</span>
    </div>

    <label class="field-label" style="left:187px;top:372px;">Description:</label>
    <div class="field field-description">1 Large Stove</div>

    <div class="update-button">UPDATE YOUR DETAILS</div>

    <h2 class="section-title drivers-title">DRIVERS IN YOUR AREA</h2>
    <p class="drivers-note">Please stay on this Page and be patient,While we contact the drives and find you one ASAP</p>

    <div class="drivers-table">
      <div class="table-head">
        <span class="col-name">NAME</span>
        <span class="col-distance">DISTANCE(KM)</span>
        <span class="col-time">AGREED PICK-UP TIME</span>
      </div>
      <div class="driver-row">
        <span class="col-name">Dorian Falk</span><span class="col-distance">4.04km away</span><span class="col-time">-</span>
        <span class="status-badge">Pending</span>
      </div>
      <div class="driver-row">
        <span class="col-name">Owen Rusk</span><span class="col-distance">5.7km away</span><span class="col-time">-</span>
        <span class="status-badge">Pending</span>
      </div>
      <div class="driver-row">
        <span class="col-name">Milo Varga</span><span class="col-distance">11.13km away</span><span class="col-time">-</span>
        <span class="status-badge">Pending</span>
      </div>
      <div class="driver-row">
        <span class="col-name">Pete Lorrimer</span><span class="col-distance">11.91km away</span><span class="col-time">-</span>
        <span class="status-badge">Pending</span>
      </div>
    </div>
  </main>

  <footer class="site-footer">
    <p class="copyright">© Copyright 2017 Bravuk. All Rights Reserved</p>
  </footer>
</body>
</html>
```